KORV PTY LTD - Business Cards

Design a modern business card - using the attached Designs.
Same design as on the front, apart from the names/numbers/emails to be different.
We want the cards to be very glossy to stand out, do I think the simple black/white/metallic will be effective.
Both lots of details below:

Tom Wrenshaw
Director
tom_korv@nulvane.com
0438 274 093

Lewis Corbyn
Director
lewis_korv@nulvane.com
0419 385 642

Industry/Entity Type

Business

```html
<!DOCTYPE html>
<html lang="en">
<head>
<meta charset="utf-8">
<title>KORV PTY LTD – Business Cards</title>
<link rel="stylesheet" href="https://fonts.googleapis.com/css2?family=Noto+Serif:wght@400;700&family=Open+Sans:wght@400&display=swap">
<style>
  :root {
    --page: #e4e2df;
    --card-white: #ffffff;
    --card-grey: #b3b3b3;
    --charcoal: #34383b;
    --steel: #9c9fa1;
    --divider: #d4d4d4;
    --ink: #1e1e1e;
    --ink-soft: #3a3a3a;
    --ghost: #4a4e51;
  }
  * { margin: 0; padding: 0; box-sizing: border-box; }
  html, body {
    width: 1200px; height: 470px; overflow: hidden;
    background: var(--page);
  }
  .sheet {
    position: relative; width: 1200px; height: 470px;
  }
  .card {
    position: absolute; top: 70px;
    width: 540px; height: 330px;
    overflow: hidden;
    box-shadow: 0 6px 18px rgba(0,0,0,0.25);
  }
  .card--front { left: 40px; background: var(--card-white); }
  .card--back { left: 620px; background: var(--card-grey); }

  .card__swoosh { position: absolute; inset: 0; }

  .brand {
    position: absolute; display: flex; align-items: center; gap: 10px;
    font-family: "Noto Serif", serif; font-weight: 700; color: var(--charcoal);
  }
  .brand__dot { border-radius: 50%; background: var(--charcoal); flex: none; }
  .card--front .brand { left: 46px; top: 112px; font-size: 36px; letter-spacing: 2px; }
  .card--front .brand__dot { width: 22px; height: 22px; }

  .divider {
    position: absolute; left: 262px; top: 42px; width: 1px; height: 140px;
    background: var(--divider);
  }
  .contact {
    position: absolute; left: 285px; top: 50px;
    font-family: "Noto Serif", serif; color: var(--ink);
  }
  .contact__name { font-size: 22px; font-weight: 400; }
  .contact__role { font-size: 13px; margin-top: 6px; color: var(--ink-soft); }
  .contact__list { list-style: none; margin-top: 32px; font-family: "Open Sans", sans-serif; font-size: 15px; }
  .contact__item { display: flex; align-items: center; gap: 7px; margin-bottom: 4px; }
  .contact__icon { width: 12px; height: 12px; flex: none; }

  .ghost-name {
    position: absolute; right: 20px; bottom: 24px;
    font-family: "Noto Serif", serif; font-weight: 700; font-size: 30px;
    color: var(--ghost); letter-spacing: 2px;
  }

  .card--back .brand {
    left: 50%; top: 50%; transform: translate(-50%, -50%);
    font-size: 40px; letter-spacing: 2px; white-space: nowrap;
  }
  .card--back .brand__dot { width: 26px; height: 26px; }
</style>
</head>
<body>
<main class="sheet">
  <section class="card card--front" aria-label="Business card front">
    <svg class="card__swoosh" viewBox="0 0 540 330" aria-hidden="true">
      <path d="M0,300 Q280,286 540,190 V330 H0 Z" fill="var(--charcoal)"/>
      <path d="M0,292 Q280,278 540,181" fill="none" stroke="var(--steel)" stroke-width="3"/>
      <path d="M0,314 Q280,300 540,226" fill="none" stroke="#ffffff" stroke-width="2"/>
      <path d="M0,317 Q280,303 540,229 V236 Q280,312 0,330 Z" fill="var(--steel)"/>
    </svg>

    <div class="brand"><span class="brand__dot"></span>KORV</div>
    <div class="divider"></div>

    <div class="contact">
      <h1 class="contact__name">Lewis Corbyn</h1>
      <p class="contact__role">Director</p>
      <ul class="contact__list">
        <li class="contact__item">
          <svg class="contact__icon" viewBox="0 0 12 12" aria-hidden="true"><circle cx="6" cy="6" r="5.3" fill="none" stroke="var(--ink)" stroke-width="1.1"/><path d="M4,3.2 L5,3 L5.6,4.6 L4.9,5.1 Q5.4,6.4 6.8,7.1 L7.3,6.4 L8.9,7 L8.7,8.1 Q6.6,8.6 4.9,6.9 Q3.5,5.3 4,3.2 Z" fill="var(--ink)"/></svg>
          <span>0419 385 642</span>
        </li>
        <li class="contact__item">
          <svg class="contact__icon" viewBox="0 0 12 12" aria-hidden="true"><rect x="0.6" y="2.2" width="10.8" height="7.6" rx="1" fill="var(--ink)"/><path d="M1,2.8 L6,6.6 L11,2.8" fill="none" stroke="#fff" stroke-width="1"/></svg>
          <span>lewis_korv@nulvane.com</span>
        </li>
      </ul>
    </div>

    <div class="ghost-name" aria-hidden="true">KORV</div>
  </section>

  <section class="card card--back" aria-label="Business card back">
    <div class="brand"><span class="brand__dot"></span>KORV PTY LTD</div>
  </section>
</main>
</body>
</html>
```